TalkHarbor - Language Coaching Services

Sleek, innovative, trendy design for Language Coaching business.

TalkHarbor is a new UK based company that provides Language Coaching services. We offer highly personalized on-line and face to face language courses. We also impart learning techniques workshops based on the latest neuroscience research for second-language acquisition.

Target Market(s)

See attached info

Industry/Entity Type

Consulting

Contact Information for Business Card

TalkHarbor
DaniaKV@talkharbor.co.uk
TalkHarbor.co.uk
London, UK

Font styles to use
Sans Serif

```html
<!DOCTYPE html>
<html lang="en">
<head>
<meta charset="utf-8">
<title>TalkHarbor Business Card</title>
<link href="https://fonts.googleapis.com/css2?family=Oswald:wght@500&family=PT+Sans:wght@400;700&display=swap" rel="stylesheet">
<style>
  :root {
    --stage: #2b2c2e;
    --card: #ffffff;
    --brand: #1f7fa6;
    --name-blue: #4a86d4;
    --rule-blue: #5b8fd6;
    --ink: #1f1f1f;
    --icon: #6f9ad8;
  }
  * { margin: 0; padding: 0; box-sizing: border-box; }
  html, body {
    width: 1200px; height: 1200px; overflow: hidden;
    background: var(--stage);
    font-family: "PT Sans", sans-serif;
  }
  .card {
    position: absolute; left: 160px;
    width: 880px; height: 503px;
    background: var(--card);
    box-shadow: 0 6px 18px rgba(0,0,0,0.45);
  }
  .card--front { top: 72px; }
  .card--back { top: 625px; }

  .front-mark {
    position: absolute; left: 50%; top: 50%;
    transform: translate(-50%, -50%);
    display: flex; align-items: center; gap: 22px;
  }
  .brand-dot {
    width: 120px; height: 120px; border-radius: 50%;
    border: 12px solid var(--brand);
  }
  .brand-name {
    font-family: "PT Sans", sans-serif; font-weight: 400;
    color: var(--brand); letter-spacing: 2px; white-space: nowrap;
  }
  .front-mark .brand-name { font-size: 52px; }

  .back-mark {
    position: absolute; right: 62px; top: 60px;
    display: flex; flex-direction: column; align-items: center; gap: 18px;
  }
  .back-mark .brand-dot { width: 150px; height: 150px; border-width: 11px; }
  .back-mark .brand-name { font-size: 56px; }

  .person { position: absolute; left: 66px; top: 300px; }
  .person__name {
    font-family: "Oswald", sans-serif; font-weight: 500;
    font-size: 44px; line-height: 1; color: var(--name-blue);
    letter-spacing: 0.5px; text-transform: uppercase;
  }
  .person__title { font-size: 23px; color: var(--ink); margin-top: 4px; }

  .rule {
    position: absolute; left: 56px; right: 60px; top: 386px;
    height: 4px; background: var(--rule-blue);
  }

  .contacts {
    position: absolute; left: 62px; top: 400px;
    list-style: none; font-size: 24px; color: var(--ink); line-height: 30px;
  }
  .contacts li { display: flex; align-items: center; gap: 16px; white-space: nowrap; }
  .contacts svg { width: 18px; height: 18px; flex: none; }

  .address {
    position: absolute; right: 60px; bottom: 24px;
    text-align: right; font-size: 24px; line-height: 30px; color: var(--ink);
    font-style: normal;
  }
</style>
</head>
<body>

<section class="card card--front">
  <div class="front-mark">
    <div class="brand-dot"></div>
    <span class="brand-name">TalkHarbor</span>
  </div>
</section>

<section class="card card--back">
  <div class="back-mark">
    <div class="brand-dot"></div>
    <span class="brand-name">TalkHarbor</span>
  </div>

  <div class="person">
    <div class="person__name">Elin Marsh</div>
    <div class="person__title">President &amp; CEO</div>
  </div>

  <div class="rule"></div>

  <ul class="contacts">
    <li>
      <svg viewBox="0 0 24 24" aria-hidden="true"><path fill="var(--icon)" d="M6.6 10.8a15.2 15.2 0 0 0 6.6 6.6l2.2-2.2a1 1 0 0 1 1-.25 11.4 11.4 0 0 0 3.6.57 1 1 0 0 1 1 1V20a1 1 0 0 1-1 1A17 17 0 0 1 3 4a1 1 0 0 1 1-1h3.5a1 1 0 0 1 1 1c0 1.250.2 2.450.57 3.57a1 1 0 0 1-.25 1z"/></svg>
      +(000) -000- 0000
    </li>
    <li>
      <svg viewBox="0 0 24 24" aria-hidden="true"><rect x="2" y="5" width="20" height="14" fill="none" stroke="var(--icon)" stroke-width="2"/><path d="M2 5l10 8 10-8" fill="none" stroke="var(--icon)" stroke-width="2"/></svg>
      info@talkharbor.co.uk
    </li>
    <li>
      <svg viewBox="0 0 24 24" aria-hidden="true"><circle cx="12" cy="12" r="9" fill="none" stroke="var(--icon)" stroke-width="2"/><path d="M3 12h18M12 3c3 3 3 15 0 18M12 3c-3 3-3 15 0 18" fill="none" stroke="var(--icon)" stroke-width="1.5"/></svg>
      www.TalkHarbor.co.uk
    </li>
  </ul>

  <address class="address">
    Harbor House, 14 Wharf Lane,<br>
    Suite 2 London
  </address>
</section>

</body>
</html>
```